Dusty Spur Outfitters Home Page

I need a logo and page design for my home page, maybe some background color suggestions to go with it. I want the logo to project "vintage" and "western wear" but not be your typical trite western saddle and gun type thing.
http://www.dustyspuroutfitters.example/store/cart.php
Not looking for page coding just logo and other design elements to lay in over the site's template to make it "pop"
Reason: Have to finalize the design.
Target Market(s)
My customers are 70/30 men to women.
Industry/Entity Type
Gun

```html
<!DOCTYPE html>
<html lang="en">
<head>
<meta charset="utf-8">
<title>Dusty Spur Outfitters</title>
<link href="https://fonts.googleapis.com/css2?family=Source+Sans+3:wght@400;600&display=swap" rel="stylesheet">
<style>
:root{
  --red:#d0141b;
  --red-dark:#b80f15;
  --brown:#7a5a2e;
  --text:#444;
  --muted:#777;
  --grey-bg:#f2f2f2;
  --line:#e2e2e2;
  --green:#2f9a1f;
  --beige-a:#f1e3c7;
  --beige-b:#d9bb86;
  --footer-dark:#3a3a3a;
}
*{margin:0;padding:0;box-sizing:border-box}
html,body{width:794px;height:1200px;overflow:hidden;background:#fff}
body{position:relative;font-family:"Source Sans 3",sans-serif;color:var(--text)}
.abs{position:absolute}

/* header */
.brand{left:86px;top:24px;display:flex;align-items:center;gap:8px}
.brand-dot{width:26px;height:26px;border-radius:50%;background:var(--red)}
.brand-name{font-size:18px;font-weight:600;color:var(--red);white-space:nowrap}
.cart{left:536px;top:17px;display:flex;gap:8px}
.cart-label{font-size:9px;line-height:12px;color:#555;text-transform:uppercase}
.cart-count{font-size:8px;color:var(--red)}
.search-btn{left:683px;top:19px;width:22px;height:22px;background:var(--red);border-radius:2px;display:flex;align-items:center;justify-content:center}
.nav{right:88px;top:63px;display:flex;font-size:8.5px;color:#555;text-transform:uppercase}
.nav span+span::before{content:"|";margin:0 9px}
.header-rule{left:0;top:90px;width:794px;height:1px;background:var(--line)}

/* hero */
.hero{left:0;top:90px;width:794px;height:316px;background:linear-gradient(100deg,var(--beige-a) 0%,#ead6b0 50%,#c9a978 100%)}
.hero-figure{left:436px;top:90px;width:284px;height:316px;background:linear-gradient(180deg,#5a5550 0%,#2a2826 55%,#7a746c 100%);opacity:.85}
.hero-title{left:100px;top:138px;width:300px;text-align:center;font-size:35px;line-height:40px;font-weight:600;color:var(--brown);text-transform:uppercase}
.hero-copy{left:110px;top:232px;width:280px;text-align:center;font-size:8.5px;line-height:16.5px;color:#4a3a24}
.hero-btn{left:210px;top:298px;width:79px;height:27px;background:var(--red);color:#fff;font-size:10.5px;display:flex;align-items:center;justify-content:center;border-radius:2px}
.slide-arrow{top:228px;width:30px;height:32px;background:rgba(90,90,90,.7);display:flex;align-items:center;justify-content:center}

/* sidebar */
.sidebar{left:86px;top:446px;width:146px;height:353px;background:var(--grey-bg);padding:13px 8px 0 13px}
.sidebar h2{font-size:13px;font-weight:400;color:var(--red);padding-bottom:6px;border-bottom:1px solid #ddd;margin-right:0}
.cat-list{list-style:none;margin-top:8px}
.cat-list li{font-size:8.5px;line-height:20.6px;color:#444;padding-left:16px;position:relative}
.cat-list li::before{content:"";position:absolute;left:3px;top:10px;width:3px;height:1px;background:#aaa}

/* products */
.section-title{left:246px;top:455px;font-size:13.5px;color:#333}
.section-title em{font-style:normal;color:var(--red)}
.section-rule{left:246px;top:478px;width:463px;height:1px;background:var(--line)}
.section-next{left:687px;top:452px;width:20px;height:17px;background:#eee;display:flex;align-items:center;justify-content:center}
.card{width:147px;height:219px;background:linear-gradient(160deg,var(--beige-a),var(--beige-b))}
.card-photo{position:absolute;left:9px;top:8px;width:129px;height:133px;background:linear-gradient(180deg,#a8d4e6,#8cc6dd)}
.card-name{position:absolute;left:10px;top:152px;font-size:9.5px;color:var(--red);text-transform:uppercase}
.card-desc{position:absolute;left:10px;top:166px;font-size:8.5px;color:#555}
.card-price{position:absolute;left:10px;top:184px;font-size:18px;color:var(--green)}
.card-price sup{font-size:9px}
.card-btn{position:absolute;left:72px;top:189px;width:63px;height:20px;background:var(--red);color:#fff;font-size:8px;display:flex;align-items:center;justify-content:center;border-radius:1px}

/* footer */
.footer{left:0;top:986px;width:794px;height:176px;background:var(--grey-bg)}
.f-col h3{font-size:11.5px;font-weight:400;color:#444;margin-bottom:10px}
.f-col ul{list-style:none}
.f-col li{font-size:8.5px;line-height:20px;color:var(--muted)}
.f-divider{top:1008px;width:1px;height:126px;background:#e0e0e0}
.email{left:562px;top:1035px;width:145px;height:21px;background:#fff;font-size:7.5px;font-style:italic;color:#aaa;padding:6px 10px}
.subscribe{right:88px;top:1066px;font-size:8.5px;color:var(--green)}
.follow{left:564px;top:1088px;font-size:11.5px;color:#444}
.social{top:1112px;width:18px;height:18px;border-radius:50%;background:#8a8a8a}
.bottom-bar{left:0;top:1162px;width:794px;height:38px;background:var(--footer-dark);color:#ddd;font-size:8px;display:flex;align-items:center;justify-content:center;gap:6px}
</style>
</head>
<body>

<header>
  <div class="abs brand"><span class="brand-dot"></span><span class="brand-name">Dusty Spur Outfitters</span></div>
  <a class="abs cart" href="http://www.dustyspuroutfitters.example/store/cart.php" style="text-decoration:none">
    <svg width="26" height="24" viewBox="0 0 26 24"><path d="M1 3h4l3 11h12l3-8H7" fill="none" stroke="#d0141b" stroke-width="2.2" stroke-linejoin="round"/><circle cx="10" cy="19" r="2" fill="#d0141b"/><circle cx="18" cy="19" r="2" fill="#d0141b"/></svg>
    <div><div class="cart-label">My Shopping Cart</div><div class="cart-count">(0) Item</div></div>
  </a>
  <div class="abs search-btn"><svg width="10" height="10" viewBox="0 0 10 10"><circle cx="4" cy="4" r="2.8" fill="none" stroke="#fff" stroke-width="1.5"/><path d="M6 6l3 3" stroke="#fff" stroke-width="1.6"/></svg></div>
  <nav class="abs nav"><span>About</span><span>Sizing</span><span>Returns</span><span>Shipping</span><span>Links</span><span>Contact</span></nav>
  <div class="abs header-rule"></div>
</header>

<section>
  <div class="abs hero" role="img" aria-label="Aged parchment grid background with stitched ribbon, zipper and buttons"></div>
  <div class="abs hero-figure" role="img" aria-label="Photo of a man in a black shirt and wide-brim hat"></div>
  <h1 class="abs hero-title">Men's Western<br>Wear</h1>
  <p class="abs hero-copy">Lorem ipsum dolor sit amet, consectetur adipisicing elit, sed do eiusmod tempor incididunt ulabore et dolore magna aliqua. Ut enim ad minim veniam, quis nostrud</p>
  <div class="abs hero-btn">Shop Now!</div>
  <div class="abs slide-arrow" style="left:0"><svg width="10" height="16" viewBox="0 0 10 16"><path d="M8 2L2 8l6 6" fill="none" stroke="#fff" stroke-width="2"/></svg></div>
  <div class="abs slide-arrow" style="left:764px"><svg width="10" height="16" viewBox="0 0 10 16"><path d="M2 2l6 6-6 6" fill="none" stroke="#fff" stroke-width="2"/></svg></div>
</section>

<aside class="abs sidebar">
  <h2>Categorie</h2>
  <ul class="cat-list">
    <li>Boots</li><li>Men's Western Wear</li><li>Women's Western Wear</li><li>Brand New Arrivals</li><li>CLEARANCE</li><li>T-Shirts</li><li>Vests</li><li>Accessories</li><li>Jackets</li><li>BELTS, Hand Bags</li><li>Leather On Sale!</li><li>Pants</li><li>Short Sleeves</li><li>Big and Tall</li><li>Jeans</li>
  </ul>
</aside>

<main>
  <h2 class="abs section-title">Featured <em>Products</em></h2>
  <div class="abs section-next"><svg width="6" height="8" viewBox="0 0 6 8"><path d="M1 1l3 3-3 3" fill="none" stroke="#bbb" stroke-width="1.4"/></svg></div>
  <div class="abs section-rule"></div>

  <div class="abs card" style="left:245px;top:494px"><div class="card-photo" role="img" aria-label="Man in a brown western bib shirt and hat"></div><div class="card-name">Product Name</div><div class="card-desc">Neque porro quisquam est</div><div class="card-price">$25.<sup>00</sup></div><div class="card-btn">Add to Cart</div></div>
  <div class="abs card" style="left:404px;top:494px"><div class="card-photo" role="img" aria-label="Woman in a red patterned blouse"></div><div class="card-name">Product Name</div><div class="card-desc">Neque porro quisquam est</div><div class="card-price">$25.<sup>00</sup></div><div class="card-btn">Add to Cart</div></div>
  <div class="abs card" style="left:562px;top:494px"><div class="card-photo" role="img" aria-label="Back view of a man in a white shirt and grey trousers"></div><div class="card-name">Product Name</div><div class="card-desc">Neque porro quisquam est</div><div class="card-price">$25.<sup>00</sup></div><div class="card-btn">Add to Cart</div></div>
  <div class="abs card" style="left:245px;top:730px"><div class="card-photo" style="background:linear-gradient(180deg,#eceff2,#d8dde3)" role="img" aria-label="Dark blue denim jeans, back view"></div><div class="card-name">Product Name</div><div class="card-desc">Neque porro quisquam est</div><div class="card-price">$25.<sup>00</sup></div><div class="card-btn">Add to Cart</div></div>
  <div class="abs card" style="left:404px;top:730px"><div class="card-photo" role="img" aria-label="Turquoise fringed leather handbag"></div><div class="card-name">Product Name</div><div class="card-desc">Neque porro quisquam est</div><div class="card-price">$25.<sup>00</sup></div><div class="card-btn">Add to Cart</div></div>
  <div class="abs card" style="left:562px;top:730px"><div class="card-photo" style="background:linear-gradient(180deg,#f7f7f7,#e9e9e9)" role="img" aria-label="Man in a black vest and hat"></div><div class="card-name">Product Name</div><div class="card-desc">Neque porro quisquam est</div><div class="card-price">$25.<sup>00</sup></div><div class="card-btn">Add to Cart</div></div>
</main>

<footer>
  <div class="abs footer"></div>
  <div class="abs f-col" style="left:86px;top:1006px"><h3>Information</h3><ul><li>About Us</li><li>Customer Service</li><li>Privacy Policy</li><li>Site Map</li><li>Orders and Returns</li><li>Contact Us</li></ul></div>
  <div class="abs f-divider" style="left:201px"></div>
  <div class="abs f-col" style="left:246px;top:1007px"><h3>Why buy from us</h3><ul><li>Shipping &amp; Returns</li><li>Secure Shopping</li><li>International Shipping</li><li>Affiliates</li><li>Group Sales</li></ul></div>
  <div class="abs f-divider" style="left:366px"></div>
  <div class="abs f-col" style="left:404px;top:1006px"><h3>My account</h3><ul><li>Sign In</li><li>View Cart</li><li>My Wishlist</li><li>Track My Order</li><li>Help</li></ul></div>
  <div class="abs f-divider" style="left:517px"></div>
  <div class="abs f-col" style="left:562px;top:1006px"><h3>Newsletter</h3></div>
  <div class="abs email">Enter your Email...</div>
  <div class="abs subscribe">&gt; Subscribe</div>
  <div class="abs follow">Follow us</div>
  <span class="abs social" style="left:563px"></span>
  <span class="abs social" style="left:585px"></span>
  <span class="abs social" style="left:608px"></span>
  <span class="abs social" style="left:629px"></span>
  <div class="abs bottom-bar"><span>Copyright © 2014</span><span>Your Site Name</span><span>All Rights Reserved.</span></div>
</footer>

</body>
</html>
```